Small legal and financial translation company needs Squarespace website, brochure and logo

Hello,
We are Lumarin Services (www.lumarinservices-example.com), a boutique legal and financial translation company. We offer our services mainly to Spanish customers. Our primary line of business is the translation of financial statements, but we translate a wide variety legal and financial texts.
The project we are offering comprises three parts: a redo of the current website, an informational brochure for potential customer and a logo design. These three parts should provide a consistent image. We would develop content soon.
We are looking for a website that would look like a typical law firm website, nothing too fancy. Right now, it is in English, Spanish and French, although the new site need only be in English and Spanish. There must be good toggling between the English and Spanish versions. There would be no need for tie-ins to social media and it would not contain a blog. Basically, a static site. We aren't interesting in driving traffic to the site or SEO, as we will contact nearly all potential customers beforehand. The website must be built in Squarespace to enable a smooth transition. The content would be similar to the current page, we'll be working on the exact content, but a rough draft is attached.
The brochure will be some three pages and would introduce the company to potential customers, using similar images as the website and the logo to be designed.
The only specifications for the logo is, as the website and brochure, it convey a sense of security and trust.
Feel free to ask with any questions as this is the first time we have used this platform.
Thank you!
Updates

I've added a more or less final version for the text in the brochure and updated the brief. Added Wednesday, June 10, 2015

Target Market(s)

Spanish law firms, auditors, accountants, banks, investment firms

Industry/Entity Type

Finance

Logo Text

Lumarin Services

Number of Pages Required

5+ page

Font styles to use
Serif

Requirements
Must have
• The website must be built in Squarespace and have a good option to toggle between English and Spanish versions.
• Brochure must be in both English and Spanish, I'm attaching a rough draft of the information that it will probably have. This should give an idea about what to include and the spacing. I will update it to include the final information.
Nice to have
• Would be nice to have some quality finance- and legal-related images
Should not have
• Vibrant colours

```html
<!DOCTYPE html>
<html lang="en">
<head>
<meta charset="utf-8">
<title>Lumarin Services — Who we are</title>
<link rel="stylesheet" href="https://fonts.googleapis.com/css2?family=Montserrat:wght@400;500;700;800&family=Cardo:wght@400;700&family=EB+Garamond:wght@400;500&display=swap">
<style>
  :root {
    --page-bg: #ededed;
    --teal: #2aa3ad;
    --teal-dark: #1b7f86;
    --logo-blue: #a9dcea;
    --ink: #3b3b3b;
    --ink-strong: #2a2a2a;
    --muted: #9a9a9a;
    --footer-top: #333333;
    --footer-bottom: #1f1f1f;
    --white: #ffffff;
  }
  * { box-sizing: border-box; margin: 0; padding: 0; }
  html, body { width: 1116px; height: 1200px; overflow: hidden; }
  body { background: var(--page-bg); font-family: "Cardo", Georgia, serif; color: var(--ink); position: relative; }

  .hero {
    position: absolute; left: 0; top: 0; width: 1116px; height: 405px;
    background: linear-gradient(160deg, #3a3a3a 0%, #8d8d8d 35%, #a9a9a9 50%, #6b6b6b 70%, #2f2f2f 100%);
  }
  .brand {
    position: absolute; left: 16px; top: 18px;
    font-family: "Cardo", Georgia, serif; font-weight: 400; font-size: 26px;
    color: var(--logo-blue); line-height: 1;
  }
  .top-nav { position: absolute; right: 18px; top: 45px; display: flex; gap: 26px; }
  .top-nav a {
    font-family: "Montserrat", Arial, sans-serif; font-weight: 700; font-size: 10.5px;
    letter-spacing: 1.3px; color: var(--white); text-decoration: none;
  }
  .hero-title {
    position: absolute; left: 0; width: 1116px; top: 178px; text-align: center;
    font-family: "Montserrat", Arial, sans-serif; font-weight: 800; font-size: 51px;
    letter-spacing: 4px; color: var(--white);
  }

  .side-nav { position: absolute; left: 169px; top: 482px; }
  .side-nav .lang { font-family: "EB Garamond", Georgia, serif; font-size: 19px; color: var(--teal-dark); margin-bottom: 6px; }
  .side-nav a {
    display: block; font-family: "Montserrat", Arial, sans-serif; font-size: 11px;
    letter-spacing: 1.8px; line-height: 13px; color: var(--muted); text-decoration: none;
    margin-bottom: 9px; text-transform: uppercase;
  }
  .side-nav a.current { color: var(--ink-strong); }

  .content { position: absolute; left: 375px; top: 484px; width: 560px; }
  .content h1 { font-family: "EB Garamond", Georgia, serif; font-weight: 400; font-size: 35px; color: var(--teal); margin-bottom: 20px; }
  .content p { font-size: 15.5px; line-height: 19.5px; letter-spacing: 0.9px; color: var(--ink); }
  .content strong { font-weight: 700; color: var(--ink-strong); }

  .stats { position: absolute; left: 377px; top: 737px; display: flex; gap: 10px; }
  .stat { position: relative; width: 183px; height: 120px; overflow: hidden; }
  .stat .photo { position: absolute; inset: 0; }
  .stat-1 .photo { background: linear-gradient(180deg, #cfcfcf 0%, #8a8a8a 55%, #3e3e3e 100%); }
  .stat-2 .photo { background: linear-gradient(180deg, #9a9a9a 0%, #c9c9c9 50%, #5a5a5a 100%); }
  .stat-3 .photo { background: linear-gradient(180deg, #e0e0e0 0%, #8e8e8e 50%, #2e2e2e 100%); }
  .stat .band {
    position: absolute; left: 0; right: 0; top: 40px; height: 49px;
    background: rgba(255,255,255,0.72); text-align: center; font-family: "EB Garamond", Georgia, serif;
  }
  .stat .big { font-size: 21px; color: var(--teal-dark); line-height: 22px; margin-top: 6px; }
  .stat .small { font-size: 10.5px; color: #333; line-height: 11px; }
  .stat-2 .band { top: 30px; height: 62px; }
  .stat-2 .big { margin-top: 0; }

  .footer-top { position: absolute; left: 0; top: 1080px; width: 1116px; height: 52px; background: var(--footer-top); }
  .footer-bottom { position: absolute; left: 0; top: 1132px; width: 1116px; height: 68px; background: var(--footer-bottom); }
</style>
</head>
<body>
  <header class="hero">
    <div class="hero-photo" role="img" aria-label="Black and white upward view of city skyscrapers" style="position:absolute;inset:0;"></div>
    <div class="brand">Lumarin Services</div>
    <nav class="top-nav">
      <a href="#">HOME</a>
      <a href="#">ENGLISH</a>
      <a href="#">SPANISH</a>
    </nav>
    <h2 class="hero-title">WHO WE ARE</h2>
  </header>

  <nav class="side-nav">
    <div class="lang">English</div>
    <a class="current" href="#">Who we are</a>
    <a href="#">Benefits</a>
    <a href="#">Legal translation</a>
    <a href="#">Financial<br>translation</a>
    <a href="#">Contact</a>
  </nav>

  <main class="content">
    <h1>Who we are</h1>
    <p>We are a small, highly qualified group of professionals with <strong>backgrounds in law, financial services and translation</strong> that boasts experience in global consulting and auditing firms, law firms and companies from a <strong>wide cross-section of industries</strong>. Sensitive to the workings of the world of finance, accounting and law, we are <strong>detail-oriented experts</strong> striving to facilitate understanding among investors, companies and international organisations:</p>
  </main>

  <section class="stats">
    <div class="stat stat-1">
      <div class="photo" role="img" aria-label="Grey skyscrapers under a cloudy sky"></div>
      <div class="band"><div class="big">over 30 years</div><div class="small">of combined experience</div></div>
    </div>
    <div class="stat stat-2">
      <div class="photo" role="img" aria-label="City street lined with office towers"></div>
      <div class="band"><div class="big">serving</div><div class="small">Big 4 firms, leading international<br>law firms and banks and Meridia 40<br>listings and blue chips</div></div>
    </div>
    <div class="stat stat-3">
      <div class="photo" role="img" aria-label="Modern glass office buildings"></div>
      <div class="band"><div class="big">over a milion</div><div class="small">words translated annually</div></div>
    </div>
  </section>

  <footer>
    <div class="footer-top"></div>
    <div class="footer-bottom"></div>
  </footer>
</body>
</html>
```